Logo and packaging design for a food brand: Noble Drippings

Dear designer,

I'm located in Vancouver, British Columbia, Canada, and I'm launching a brand of products made of beef tallow. It's called Noble Drippings. I'm ultimately looking for a designer that can help me build the brand and create a series of products.

Here is what I need at this point:

- A logo for Noble Drippings (playing with the letters N and D - sketch using ChatGPT attached)
- A packaging design for the PREMIUM WAGYU TALLOW - 235 ml (= 8 oz: https://www.vesselmartexample.ca/item/Q-40211K-ZT/containers/glass-jar-8-oz-dark-cap?ref=WX882)
- Glass jar with a label all around it and a lid seal label
- Primary colours: black, white, gold
- Secondary colours if needed: Canada red and light grey
- Fonts: not specified, looking forward to your inputs on what works
- Please refer to our #1 competitor as reference: https://www.ridgelinemeatworks-example.com/collections/products (we like their design style as well)
- #2 competitor to be used as reference: https://lardhollow-example.com/products/1-jar-14-0-oz-organic-grass-fed-beef-tallow

- Information for the packaging:
PREMIUM WAGYU BEEF TALLOW
100% PURE
(optional) PRODUCED IN CANADA
NUTRITIONAL VALUE (we don't have the numbers yet, but please create a placeholder/mockup for this section)
* You can also add more information following the example from our Competitor 01

- Please feel free to improve the logo, but keep the concept of Noble Drippings (or ND) + the face of a bull
- Finally, I'd also love to see two colour schemes: one dark and one bright - I hope it's not asking too much

Target Market(s)

North America

Industry/Entity Type

Food

Font styles to use
Sans Serif
Script

Colors
FFC000
F8CF3A
FAE287
FDF2CF
FEFAEE

Requirements
Must have
• Incorporate gold, black and white
Nice to have
• Play with the letters ND in the logo (company name: Noble Drippings)
Should not have
• Many colours

```html
<!DOCTYPE html>
<html lang="en">
<head>
<meta charset="utf-8">
<title>Noble Drippings – Wagyu Beef Tallow Label</title>
<link href="https://fonts.googleapis.com/css2?family=Montserrat:wght@600;700;900&family=Saira+Condensed:wght@400&display=swap" rel="stylesheet">
<style>
  :root {
    --bg: #f8f8f8;
    --ink: #0a0a0a;
    --paper: #ffffff;
    --gold: #d1aa00;
    --rule: #8a8a8a;
  }
  * { margin: 0; padding: 0; box-sizing: border-box; }
  html, body { width: 1200px; height: 1200px; overflow: hidden; background: var(--bg); }
  .canvas { position: relative; width: 1200px; height: 1200px; font-family: "Montserrat", sans-serif; color: var(--ink); }

  .brand-mark { position: absolute; border: 7px solid var(--ink); border-radius: 50%; }
  .brand-name { position: absolute; font-family: "Saira Condensed", sans-serif; font-weight: 400; color: var(--ink); white-space: nowrap; line-height: 1; }

  .hero-mark { left: 119px; top: 134px; width: 244px; height: 244px; }
  .hero-name { left: 392px; top: 196px; font-size: 120px; letter-spacing: -1px; }

  .label { position: absolute; left: 203px; top: 479px; width: 877px; height: 402px; border: 1px solid var(--rule); background: var(--paper); overflow: hidden; }
  .label-front { position: absolute; left: 0; top: 0; width: 427px; height: 100%; overflow: hidden; }
  .label-header { position: absolute; left: 0; top: 0; width: 100%; height: 126px; border-bottom: 1px solid var(--rule); }
  .label-mark { left: 26px; top: 13px; width: 100px; height: 100px; border-width: 4px; }
  .label-name { left: 138px; top: 42px; font-size: 46px; letter-spacing: -0.5px; }

  .product-name { position: absolute; left: 18px; top: 146px; font-weight: 900; font-size: 88px; line-height: 1; letter-spacing: -1px; white-space: nowrap; }
  .product-band { position: absolute; left: 0; top: 232px; width: 100%; height: 60px; background: var(--gold); color: var(--paper); font-weight: 900; font-size: 49px; line-height: 60px; padding-left: 20px; letter-spacing: -0.5px; white-space: nowrap; }

  .ingredients-title { position: absolute; left: 22px; top: 318px; color: var(--gold); font-weight: 700; font-size: 21px; white-space: nowrap; }
  .ingredients-list { position: absolute; left: 22px; top: 346px; font-weight: 700; font-size: 16px; white-space: nowrap; }
  .net-weight { position: absolute; left: 0; top: 378px; width: 121px; height: 20px; background: var(--ink); color: var(--paper); font-weight: 700; font-size: 11px; line-height: 20px; padding-left: 22px; white-space: nowrap; }
  .origin { position: absolute; right: 8px; top: 382px; color: var(--gold); font-weight: 600; font-size: 11px; white-space: nowrap; }

  .label-back { position: absolute; left: 427px; top: 0; width: 450px; height: 402px; background: var(--ink); }
</style>
</head>
<body>
<main class="canvas">
  <section class="brand-lockup">
    <div class="brand-mark hero-mark"></div>
    <div class="brand-name hero-name">Noble Drippings</div>
  </section>

  <section class="label">
    <div class="label-front">
      <header class="label-header">
        <div class="brand-mark label-mark"></div>
        <div class="brand-name label-name">Noble Drippings</div>
      </header>
      <h1 class="product-name">WAYGU</h1>
      <div class="product-band">BEEF TALLOW</div>
      <p class="ingredients-title">INGREDIATES :</p>
      <p class="ingredients-list">Rendered Waygu Beef Fat</p>
      <div class="net-weight">NET WT 42 OZ</div>
      <p class="origin">Manufactured in Canada</p>
    </div>

    <div class="label-back">
      <svg class="nutrition-placeholder" width="450" height="402" viewBox="0 0 450 402">
        <g fill="none" stroke="#ffffff">
          <rect x="38.5" y="53.5" width="376" height="179" stroke-width="1"/>
          <g stroke-width="3">
            <line x1="47" y1="70" x2="406" y2="70"/>
            <line x1="47" y1="86" x2="406" y2="86"/>
            <line x1="47" y1="103" x2="406" y2="103"/>
            <line x1="47" y1="120" x2="406" y2="120"/>
            <line x1="47" y1="149" x2="406" y2="149"/>
            <line x1="47" y1="164" x2="406" y2="164"/>
            <line x1="47" y1="181" x2="406" y2="181"/>
            <line x1="47" y1="198" x2="406" y2="198"/>
            <line x1="47" y1="259" x2="223" y2="259"/>
            <line x1="47" y1="275" x2="223" y2="275"/>
            <line x1="47" y1="292" x2="223" y2="292"/>
            <line x1="47" y1="309" x2="223" y2="309"/>
            <line x1="47" y1="326" x2="223" y2="326"/>
            <line x1="47" y1="343" x2="223" y2="343"/>
          </g>
        </g>
        <rect x="277" y="259" width="133" height="88" fill="#ffffff"/>
      </svg>
    </div>
  </section>
</main>
</body>
</html>
```